VFX Company Business Card Design Project

The Kestrel Works is a decentralized Visual Effects Studio servicing the television and feature film industries.
Project Brief:
Take our logo that was previously designed on Pencil Harbor and make a double sided business card.
Requirements:
- Card MUST be double sided.
- Front of card MUST have the yellow part of our logo against the dark grey background.
- Back of card is completely up to the designer.
- Back of card must include the complete company logo.
Please follow these File Preparation guidelines:
http://printnook.ca/infopage?file=filetype_en&s=PrintNook_new&lang=en
Business

```html
<!DOCTYPE html>
<html lang="en">
<head>
<meta charset="utf-8">
<title>The Kestrel Works — Business Card Set</title>
<link rel="stylesheet" href="https://fonts.googleapis.com/css2?family=Jost:wght@300;400;600&display=swap">
<style>
  :root {
    --backdrop: #d9d4cc;
    --card-dark: #2b2b2b;
    --metal-top: #3a3a3a;
    --metal-bottom: #1c1c1c;
    --brand-yellow: #fcc72a;
    --brand-grey: #5f676b;
    --paper: #eef0e8;
    --ink-light: #f1f3ea;
    --ink-dark: #1e1e1e;
    --ink-muted: #c9ccc4;
  }
  * { box-sizing: border-box; margin: 0; padding: 0; }
  html, body {
    width: 1200px;
    height: 734px;
    overflow: hidden;
  }
  body {
    position: relative;
    background: var(--backdrop);
    font-family: "Jost", sans-serif;
  }
  .card {
    position: absolute;
    width: 525px;
    height: 300px;
    background: var(--card-dark);
    overflow: hidden;
  }
  .card--front   { left: 67px;  top: 43px; }
  .card--contact { left: 628px; top: 48px; background: var(--paper); }
  .card--combo   { left: 63px;  top: 381px; }
  .card--wordmark{ left: 622px; top: 387px; }

  /* Front: brand name in yellow */
  .front-name {
    position: absolute;
    inset: 0;
    display: flex;
    align-items: center;
    justify-content: center;
    color: var(--brand-yellow);
    font-weight: 600;
    font-size: 40px;
    text-transform: uppercase;
    letter-spacing: 1px;
  }

  /* Shared logo lockup */
  .brand-name {
    font-weight: 600;
    text-transform: uppercase;
    color: var(--ink-light);
    line-height: 1;
    white-space: nowrap;
  }
  .tagline {
    font-weight: 300;
    text-transform: uppercase;
    color: var(--ink-muted);
    line-height: 1;
    white-space: nowrap;
  }
  .web {
    position: absolute;
    left: 0; right: 0;
    text-align: center;
    color: var(--ink-light);
    font-size: 17px;
    letter-spacing: 3px;
  }

  /* Contact side */
  .contact-waves { position: absolute; inset: 0; }
  .contact-logo { position: absolute; left: 25px; top: 48px; }
  .contact-logo .brand-name { font-size: 31px; letter-spacing: 1px; }
  .contact-logo .tagline { font-size: 15px; letter-spacing: 6.5px; margin-top: 8px; }
  .holder { position: absolute; left: 25px; top: 156px; color: var(--ink-light); }
  .holder-name { font-size: 18px; font-weight: 400; line-height: 1.2; }
  .holder-title { font-size: 13px; margin-top: 2px; }
  .contact-list {
    position: absolute;
    right: 33px;
    top: 170px;
    list-style: none;
    text-align: right;
    color: var(--ink-dark);
    font-size: 13.5px;
  }
  .contact-list li {
    height: 22.5px;
    display: flex;
    align-items: center;
    justify-content: flex-end;
    gap: 6px;
  }
  .contact-list svg { width: 10px; height: 10px; fill: var(--ink-dark); }
  .address {
    position: absolute;
    right: 33px;
    top: 268px;
    color: var(--ink-dark);
    font-size: 13.5px;
    line-height: 20px;
  }

  /* Combo side */
  .combo-lockup {
    position: absolute;
    left: 38px;
    top: 118px;
    display: flex;
    align-items: center;
    gap: 22px;
  }
  .combo-dot {
    width: 58px; height: 58px;
    border-radius: 50%;
    background: var(--brand-yellow);
    flex: none;
  }
  .combo-lockup .brand-name { font-size: 27px; letter-spacing: 1px; }
  .combo-lockup .tagline { font-size: 13px; letter-spacing: 6px; margin-top: 7px; }
  .card--combo .web { top: 256px; }

  /* Wordmark side */
  .wordmark-lockup {
    position: absolute;
    left: 0; right: 0;
    top: 98px;
    text-align: center;
  }
  .wordmark-lockup .brand-name { font-size: 40px; letter-spacing: 1.5px; }
  .wordmark-lockup .tagline { font-size: 21px; letter-spacing: 9px; margin-top: 12px; }
  .card--wordmark .web { top: 256px; }
</style>
</head>
<body>

  <section class="card card--front" aria-label="Card front">
    <p class="front-name">The Kestrel Works</p>
  </section>

  <section class="card card--contact" aria-label="Contact card">
    <svg class="contact-waves" viewBox="0 0 525 300" width="525" height="300" aria-hidden="true">
      <defs>
        <linearGradient id="metal" x1="0" y1="0" x2="0" y2="1">
          <stop offset="0" stop-color="var(--metal-top)"/>
          <stop offset="1" stop-color="var(--metal-bottom)"/>
        </linearGradient>
      </defs>
      <path d="M0 0H525V110C440 112 385 140 335 190C285 235 200 262 0 266Z" fill="var(--brand-grey)"/>
      <path d="M0 0H525V96C440 98 385 126 335 176C285 221 200 246 0 250Z" fill="var(--brand-yellow)"/>
      <path d="M0 0H525V88C440 90 385 118 335 168C285 213 200 236 0 240Z" fill="url(#metal)"/>
    </svg>

    <div class="contact-logo">
      <p class="brand-name">The Kestrel Works</p>
      <p class="tagline">Virtual Studio</p>
    </div>

    <div class="holder">
      <p class="holder-name">Your Name</p>
      <p class="holder-title">Title</p>
    </div>

    <ul class="contact-list">
      <li><svg viewBox="0 0 10 10"><path d="M2 0.5L3.8 2.6 2.9 3.8C3.5 5 4.8 6.4 6.2 7.1L7.4 6.2 9.5 8 8.4 9.5C4.5 9.3 0.7 5.5 0.5 1.6Z"/></svg>0123 456789</li>
      <li><svg viewBox="0 0 10 10"><rect x="2.5" y="0.5" width="5" height="9" rx="1"/><rect x="3.4" y="1.6" width="3.2" height="5.6" fill="var(--paper)"/></svg>0123 456789</li>
      <li><svg viewBox="0 0 10 10"><path d="M0.5 2H9.5V8.5H0.5Z"/><path d="M0.8 2.3L5 5.6 9.2 2.3" fill="none" stroke="var(--paper)" stroke-width="0.9"/></svg>info@kestrelworks.com</li>
      <li><svg viewBox="0 0 10 10"><circle cx="5" cy="5" r="4.4" fill="none" stroke="var(--ink-dark)" stroke-width="1"/><path d="M0.6 5H9.4M5 0.6V9.4" stroke="var(--ink-dark)" stroke-width="0.8"/><ellipse cx="5" cy="5" rx="2" ry="4.4" fill="none" stroke="var(--ink-dark)" stroke-width="0.8"/></svg>www.kestrelworks.com</li>
    </ul>
    <p class="address">00, Complex name, City, State 0042</p>
  </section>

  <section class="card card--combo" aria-label="Card back with lockup">
    <div class="combo-lockup">
      <span class="combo-dot"></span>
      <div>
        <p class="brand-name">The Kestrel Works</p>
        <p class="tagline">Virtual Studio</p>
      </div>
    </div>
    <p class="web">www.kestrelworks.com</p>
  </section>

  <section class="card card--wordmark" aria-label="Card back with wordmark">
    <div class="wordmark-lockup">
      <p class="brand-name">The Kestrel Works</p>
      <p class="tagline">Virtual Studio</p>
    </div>
    <p class="web">www.kestrelworks.com</p>
  </section>

</body>
</html>
```